Verdant Systems Business Card

want the back of card to be blue- with the logo in the center
front of card- info plus logo (info being mailing address, email address, and website address )
4 different names with titles to have on cards
1) Calvin Borsted - Owner
2) Naomi Trelvik- Customer Relationship Specialist
3) Felix Andrade- Vice President of Sales
4) Owen Markby- Chief Technology Officer

Target Market(s)

tech company in the government/probation office industry

Industry/Entity Type

Government Office

Contact Information for Business Card

1) Calvin Borsted - Owner

Colors
0355a3
ffffff

Requirements
Must have
• back side should be blue, with the logo placed in the center
• front side needs to include both the logo, as well as company info (info should include website address, email address, and mailing address)

```html
<!DOCTYPE html>
<html lang="en">
<head>
<meta charset="utf-8">
<title>Verdant Systems Business Card</title>
<link rel="stylesheet" href="https://fonts.googleapis.com/css2?family=Libre+Baskerville&family=Roboto:wght@400&display=swap">
<style>
  :root {
    --navy: #253a6b;
    --brand-blue: #0355a3;
    --grey: #8b8b93;
    --paper: #ffffff;
    --backdrop: #a3a1a1;
    --text-grey: #6f6f78;
  }
  * { margin: 0; padding: 0; box-sizing: border-box; }
  html, body { width: 1200px; height: 1200px; overflow: hidden; }
  body { background: var(--backdrop); position: relative; font-family: "Roboto", Arial, sans-serif; }

  .card {
    position: absolute;
    width: 712px;
    height: 417px;
    background: var(--paper);
    border-radius: 22px;
    overflow: hidden;
  }
  .card--brand { left: 238px; top: 120px; background: var(--brand-blue); }
  .card--contact { left: 231px; top: 645px; }

  .wordmark {
    font-family: "Libre Baskerville", Georgia, serif;
    font-weight: 400;
    color: var(--navy);
    white-space: nowrap;
    letter-spacing: 1px;
  }

  /* back side: blue with centred mark */
  .brand-mark {
    position: absolute;
    left: 50%;
    top: 92px;
    width: 86px;
    height: 86px;
    margin-left: -43px;
    border-radius: 50%;
    background: var(--paper);
  }
  .card--brand .wordmark {
    position: absolute;
    left: 0; right: 0;
    top: 218px;
    text-align: center;
    font-size: 40px;
    color: var(--paper);
  }
  .site-line {
    position: absolute;
    left: 0; right: 0;
    top: 375px;
    display: flex;
    justify-content: center;
    align-items: center;
    gap: 22px;
    font-size: 17px;
    color: var(--paper);
  }
  .site-line .dash { width: 46px; height: 3px; background: var(--paper); border-radius: 2px; }
  .brand-band { position: absolute; left: 0; bottom: 0; height: 18px; width: 100%; display: flex; }
  .brand-band .navy { flex: 0 0 357px; background: var(--navy); }
  .brand-band .grey { flex: 1; background: var(--grey); }

  /* front side: info plus mark */
  .card--contact .wordmark {
    position: absolute;
    left: 28px;
    top: 50px;
    font-size: 30px;
  }
  .tab {
    position: absolute;
    left: -44px;
    top: 175px;
    width: 56px;
    height: 56px;
    border-radius: 50%;
    background: var(--navy);
  }
  .person { position: absolute; left: 28px; top: 188px; }
  .person-name {
    font-family: "Libre Baskerville", Georgia, serif;
    font-size: 24px;
    color: var(--navy);
    letter-spacing: 0.5px;
  }
  .person-title { margin-top: 8px; font-size: 17px; color: var(--text-grey); }
  .contacts { position: absolute; left: 28px; top: 282px; list-style: none; font-size: 18px; color: var(--text-grey); }
  .contacts li { display: flex; align-items: center; height: 26px; }
  .contacts svg { width: 16px; height: 16px; margin-right: 20px; fill: var(--navy); }
  .address { position: absolute; left: 28px; top: 365px; font-size: 18px; color: var(--text-grey); }
  .accent-disc {
    position: absolute;
    left: 430px;
    top: 35px;
    width: 330px;
    height: 330px;
    border-radius: 50%;
    border: 9px solid var(--navy);
  }
</style>
</head>
<body>

<section class="card card--brand">
  <div class="brand-mark"></div>
  <div class="wordmark">VERDANT SYSTEMS</div>
  <div class="site-line"><span class="dash"></span><span>www.HarlowenCapital.com</span><span class="dash"></span></div>
  <div class="brand-band"><span class="navy"></span><span class="grey"></span></div>
</section>

<section class="card card--contact">
  <div class="wordmark">VERDANT SYSTEMS</div>
  <div class="tab"></div>
  <div class="person">
    <div class="person-name">NAOMI TRELVIK</div>
    <div class="person-title">Customer Relationship Specialist</div>
  </div>
  <ul class="contacts">
    <li><svg viewBox="0 0 16 16" aria-hidden="true"><path d="M2 5c0-2 2-3 6-3s6 1 6 3v1h-3V5H5v1H2zM4 7h8l2 7H2z"/></svg>111-111-1111</li>
    <li><svg viewBox="0 0 16 16" aria-hidden="true"><path d="M1 3h14v10H1zM2.5 4.5 8 9l5.5-4.5v1L8 10 2.5 5.5z" fill-rule="evenodd"/></svg>naomi.t@verdantsystems.com</li>
    <li><svg viewBox="0 0 16 16" aria-hidden="true"><path d="M8 1a7 7 0 1 0 0 14A7 7 0 0 0 8 1zm0 1.5c.9 1 1.5 2.7 1.6 4.8H6.4C6.5 5.2 7.1 3.5 8 2.5zM2.6 7.3A5.5 5.5 0 0 1 5.3 3 8 8 0 0 0 4.9 7.3zm0 1.4h2.3c.1 1.7.5 3.2 1.2 4.3a5.5 5.5 0 0 1-3.5-4.3zm3.8 0h3.2c-.1 2.1-.7 3.8-1.6 4.8-.9-1-1.5-2.7-1.6-4.8zm4.7 0h2.3A5.5 5.5 0 0 1 9.9 13c.7-1.1 1.1-2.6 1.2-4.3zm0-1.4A8 8 0 0 0 10.7 3a5.5 5.5 0 0 1 2.7 4.3z"/></svg>www.verdantsystems.com</li>
  </ul>
  <div class="address">234 Anywhere St., Any City, Town, US 123456</div>
  <div class="accent-disc"></div>
</section>

</body>
</html>
```